Business Card Design needed for start up company Halvora

In need of a new business card designed for a start up company based in Sydney, Halvora is a new start up innovative Company, our mission it to make property accessible for everyday Australian and to become the leading Real Estate platform in Australia. We want it to be fresh and clean.

Industry/Entity Type

Financial

Contact Information for Business Card

Section for Name
Section for Title

HALVORA - The Strength of Pooling
Mobile:
Direct:

Font styles to use
Sans Serif

Colors
33a6d7
0692cd
0255a3
ffffff

Requirements
Must have
• Logo, all business card details

```html
<!DOCTYPE html>
<html lang="en">
<head>
<meta charset="UTF-8">
<title>Halvora Business Card</title>
<link rel="stylesheet" href="https://fonts.googleapis.com/css2?family=Open+Sans:wght@400;600;800&display=swap">
<style>
  :root {
    --sky: #33a6d7;
    --azure: #0692cd;
    --navy: #0255a3;
    --deep-navy: #143566;
    --white: #ffffff;
    --backdrop: #2b2b2d;
    --paper: #f4f5f7;
  }
  * { box-sizing: border-box; margin: 0; padding: 0; }
  html, body {
    width: 1200px; height: 900px; overflow: hidden;
    background: var(--backdrop);
    font-family: "Open Sans", sans-serif;
  }
  .canvas {
    width: 1200px; height: 900px;
    display: flex; flex-direction: column;
    align-items: center; justify-content: center; gap: 48px;
  }
  .card {
    width: 640px; height: 366px;
    position: relative; overflow: hidden;
    box-shadow: 0 12px 30px rgba(0,0,0,.45);
  }

  /* Card front: logo side */
  .card-front {
    background: linear-gradient(100deg, var(--navy) 0%, var(--deep-navy) 70%);
    display: flex; flex-direction: column; align-items: center; justify-content: center;
  }
  .brand { display: flex; align-items: center; gap: 14px; }
  .brand-dot {
    width: 58px; height: 58px; border-radius: 50%;
    background: var(--white);
  }
  .brand-name {
    font-weight: 800; font-size: 64px; letter-spacing: 1px;
    color: var(--white); line-height: 1;
  }
  .tagline {
    margin-top: 34px; font-size: 15px; color: var(--white); font-weight: 400;
  }

  /* Card back: contact side */
  .card-back { display: flex; background: var(--paper); }
  .contact-panel {
    width: 44%; height: 100%;
    background: linear-gradient(160deg, var(--sky) 0%, var(--azure) 100%);
    color: var(--white);
    padding: 78px 0 0 34px;
  }
  .person-name { font-weight: 800; font-size: 17px; letter-spacing: .5px; }
  .person-title { font-size: 15px; margin-top: 2px; }
  .address { margin-top: 28px; font-size: 14px; line-height: 1.45; }
  .contact-list { list-style: none; margin-top: 4px; font-size: 14px; line-height: 1.45; }
  .contact-list li { display: flex; align-items: center; gap: 8px; }
  .contact-list svg { width: 12px; height: 12px; flex: none; fill: var(--white); }
  .logo-panel {
    flex: 1; display: flex; align-items: center; justify-content: center;
    background: var(--paper);
  }
  .logo-panel .brand-dot { width: 48px; height: 48px; background: var(--azure); }
  .logo-panel .brand-name { font-size: 50px; color: var(--deep-navy); }
  .edge-strip { width: 18px; height: 100%; background: var(--deep-navy); }
</style>
</head>
<body>
<main class="canvas">
  <section class="card card-front">
    <div class="brand">
      <span class="brand-dot"></span>
      <span class="brand-name">HALVORA</span>
    </div>
    <p class="tagline">The Strength of Pooling</p>
  </section>

  <section class="card card-back">
    <div class="contact-panel">
      <p class="person-name">LIAM CARVER</p>
      <p class="person-title">CEO/FOUNDER</p>
      <p class="address">214 Harbourview Road<br>Sydney, NSW 2000</p>
      <ul class="contact-list">
        <li>
          <svg viewBox="0 0 24 24" aria-hidden="true"><path d="M6.6 10.8a15.1 15.1 0 0 0 6.6 6.6l2.2-2.2a1 1 0 0 1 1-.25 11.4 11.4 0 0 0 3.6.57 1 1 0 0 1 1 1V20a1 1 0 0 1-1 1A17 17 0 0 1 3 4a1 1 0 0 1 1-1h3.5a1 1 0 0 1 1 1c0 1.25.2 2.45.57 3.57a1 1 0 0 1-.25 1z"/></svg>
          612 905 4418
        </li>
        <li>
          <svg viewBox="0 0 24 24" aria-hidden="true"><path d="M7 1h10a2 2 0 0 1 2 2v18a2 2 0 0 1-2 2H7a2 2 0 0 1-2-2V3a2 2 0 0 1 2-2zm0 3v14h10V4zm5 15.5a1 1 0 1 0 0 2 1 1 0 0 0 0-2z"/></svg>
          614 273 8851
        </li>
        <li>
          <svg viewBox="0 0 24 24" aria-hidden="true"><path d="M2 5h20v14H2zm2 2v.5l8 5 8-5V7zm0 2.9V17h16V9.9l-8 5z"/></svg>
          liam@halvora.com
        </li>
        <li>
          <svg viewBox="0 0 24 24" aria-hidden="true"><path d="M12 2a10 10 0 1 0 0 20 10 10 0 0 0 0-20zm0 2c1 0 2.3 2 2.8 5H9.2C9.7 6 11 4 12 4zM4.3 11h4.7a17 17 0 0 0 0 2H4.3a8 8 0 0 1 0-2zm10.7 0h4.7a8 8 0 0 1 0 2H15a17 17 0 0 0 0-2zm-5.8 4h5.6c-.5 3-1.8 5-2.8 5s-2.3-2-2.8-5z"/></svg>
          www.halvora.com
        </li>
      </ul>
    </div>
    <div class="logo-panel">
      <div class="brand">
        <span class="brand-dot"></span>
        <span class="brand-name">HALVORA</span>
      </div>
    </div>
    <div class="edge-strip"></div>
  </section>
</main>
</body>
</html>
```